Venture 482 - Lumora Book Cover

I am looking for a Lumora book cover for my book about "Venture 482".
The Book is Titled:
Venture 482 Ascended
Shaping Outcomes: Paths To Unlocking Cosmic Truths
Author is Dorian Pell
Here is a book description that may help you understand more about it:
Inspired by the genius of Edwin Marlowe, this comprehensive guide delves into the ancient wisdom and cutting-edge science behind the 482 method, a powerful tool for manifesting your desires. Whether you're seeking personal growth, financial success, or spiritual enlightenment, this book provides advanced techniques and methods to transform your dreams into reality.
Any questions please ask.
Thanks
Owen

```html
<!DOCTYPE html>
<html lang="en">
<head>
<meta charset="utf-8">
<title>Venture 482 Ascended — Dorian Pell</title>
<link rel="stylesheet" href="https://fonts.googleapis.com/css2?family=Cinzel:wght@700;900&family=Marcellus&family=Tinos&display=swap">
<style>
  :root {
    --sky-top: #0c1d30;
    --sky-mid: #24557c;
    --sky-low: #6e9fc2;
    --horizon: #c9dbe6;
    --glow: #f2d3a8;
    --sea-mid: #2f6890;
    --sea-deep: #0b2640;
    --title-cream: #f7e4d7;
    --author-blush: #f1d6c8;
    --accent-cream: #fbf4d2;
    --shadow-ink: rgba(10, 20, 35, 0.75);
    --white: #ffffff;
  }
  * { margin: 0; padding: 0; box-sizing: border-box; }
  html, body { width: 805px; height: 1200px; overflow: hidden; background: var(--sky-top); }
  .cover {
    position: relative;
    width: 805px;
    height: 1200px;
    overflow: hidden;
  }
  .cover-art {
    position: absolute;
    inset: 0;
    background:
      radial-gradient(ellipse 260px 70px at 430px 712px, rgba(242, 211, 168, 0.85), rgba(242, 211, 168, 0) 70%),
      linear-gradient(180deg,
        var(--sky-top) 0%,
        var(--sky-mid) 28%,
        var(--sky-low) 50%,
        var(--horizon) 59%,
        var(--sky-low) 62%,
        var(--sea-mid) 74%,
        var(--sea-deep) 100%);
  }
  .text {
    position: absolute;
    left: 0;
    width: 100%;
    text-align: center;
    white-space: nowrap;
  }
  .author {
    top: 78px;
    padding-left: 30px;
    font-family: "Marcellus", serif;
    font-size: 50px;
    letter-spacing: 0.32em;
    color: var(--author-blush);
  }
  .title-word {
    top: 172px;
    font-family: "Cinzel", serif;
    font-weight: 900;
    font-size: 112px;
    line-height: 1;
    color: var(--title-cream);
    text-shadow: 0 4px 10px rgba(10, 20, 35, 0.35);
  }
  .title-number {
    top: 262px;
    font-family: "Cinzel", serif;
    font-weight: 700;
    font-size: 262px;
    line-height: 1;
    letter-spacing: -0.02em;
    color: var(--title-cream);
    text-shadow: 0 6px 14px rgba(10, 20, 35, 0.3);
  }
  .title-tag {
    top: 528px;
    padding-left: 22px;
    font-family: "Cinzel", serif;
    font-weight: 900;
    font-size: 60px;
    line-height: 1;
    letter-spacing: 0.3em;
    color: var(--accent-cream);
    text-shadow: 3px 3px 0 var(--shadow-ink);
  }
  .subtitle {
    top: 1028px;
    font-family: "Marcellus", serif;
    font-size: 33px;
    letter-spacing: 0.04em;
    color: var(--white);
  }
  .tagline {
    top: 1082px;
    font-family: "Tinos", serif;
    font-size: 27px;
    line-height: 38px;
    color: var(--white);
  }
</style>
</head>
<body>
  <main class="cover">
    <div class="cover-art" role="img" aria-label="Illustration: a lone silhouetted figure standing on mirror-still water inside a tall glowing doorway frame, red foliage at its edge, twilight blue sky, distant mountains and a warm horizon glow reflected below"></div>

    <p class="text author">DORIAN PELL</p>
    <h1 class="title">
      <span class="text title-word">VENTURE</span>
      <span class="text title-number">482</span>
      <span class="text title-tag">ASCENDED</span>
    </h1>
    <p class="text subtitle">SHAPING OUTCOMES:</p>
    <p class="text tagline">Paths to unlocking<br>cosmic truths</p>
  </main>
</body>
</html>
```